Financial Services Consultant needs a business card

We need a business card for a new consulting company based in Melbourne called
"Quelbrook Insights". Tagline is Measure, Monitor, Save
We would like to see business card designs that are in line with the minimal style of the website www.quelbrook-insights.example
The font I have used on the website is Proxima Nova and would like the same or similar font used on the business card with a minimal design in line with the website Two sided with "QUELBROOK INSIGHTS" MEASURE, MONITOR, SAVE on one side and name, title and contact details on the otther
Updates

Hi All, thanks for your submissions, much appreciated.

I have recently added some colour to my webiste, it is hex #3a7b74 for those that wish to use it
Thanks

Hi all

thanks very much for your design submissions I am very impressed and they are much appreciated.

Interms of general feedback please find below;

Colour: I am trying to stick to a minimal design and colour scheme for my website which is still under construction, up to 3 colours( www.quelbrook-insights.example) it is currently black and white with a small amount of blue/green but I am open to suggestion/interpretations for a consulting company.

Card: I dont mind if it has rounded edges or straight, I was thinking about using a letterpress card if possible

Detail: the detail on the card will include; Name, Title, Mobile, Personal Email, Business Email,Web,Business Address

Once again thanks for submissions

Industry/Entity Type

Business

```html
<!DOCTYPE html>
<html lang="en">
<head>
<meta charset="utf-8">
<title>Quelbrook Insights — Business Card</title>
<link href="https://fonts.googleapis.com/css2?family=Montserrat:wght@400;500;600&display=swap" rel="stylesheet">
<style>
  :root {
    --page-bg: #f3f3f3;
    --card-bg: #ffffff;
    --ink: #000000;
    --teal: #3a7b74;
    --mist: #e8e8e8;
    --rule: #e2e2e2;
    --frame: #bdbdbd;
    --paper-white: #ffffff;
  }
  * { box-sizing: border-box; margin: 0; padding: 0; }
  html, body {
    width: 1200px;
    height: 378px;
    overflow: hidden;
    background: var(--page-bg);
    font-family: "Montserrat", Arial, sans-serif;
    color: var(--ink);
  }
  .canvas {
    position: relative;
    width: 1200px;
    height: 378px;
  }
  .card {
    position: absolute;
    top: 8px;
    width: 566px;
    height: 362px;
    background: var(--card-bg);
    overflow: hidden;
  }
  /* Front side */
  .card--front {
    left: 10px;
    border: 1px solid var(--frame);
    box-shadow: 0 1px 2px rgba(0,0,0,0.12);
  }
  .front__name {
    position: absolute;
    left: 0; right: 0;
    top: 142px;
    text-align: center;
    font-weight: 400;
    font-size: 39px;
    letter-spacing: 1px;
    line-height: 1;
  }
  .front__tagline {
    position: absolute;
    left: 0; right: 0;
    top: 215px;
    text-align: center;
    font-weight: 600;
    font-size: 11.5px;
    letter-spacing: 0.6px;
    color: var(--teal);
  }
  /* Back side */
  .card--back {
    left: 624px;
    border: 1px solid #8a8a8a;
  }
  .back__header {
    position: absolute;
    left: 0; top: 0;
    width: 100%;
    height: 200px;
    border-bottom: 1px solid var(--rule);
  }
  .back__mark {
    position: absolute;
    left: 30px;
    top: 30px;
    width: 140px;
    height: 140px;
    background: var(--mist);
  }
  .back__brand {
    position: absolute;
    right: 22px;
    top: 92px;
    font-weight: 400;
    font-size: 30px;
    color: var(--mist);
    line-height: 1;
  }
  .back__contact {
    position: absolute;
    left: 322px;
    top: 228px;
    line-height: 1.2;
  }
  .contact__name {
    font-weight: 500;
    font-size: 16.5px;
    letter-spacing: 0.3px;
  }
  .contact__line {
    font-weight: 500;
    font-size: 13px;
  }
  .back__footer {
    position: absolute;
    left: 0; bottom: 0;
    width: 100%;
    height: 34px;
    background: var(--teal);
    color: var(--paper-white);
    font-weight: 500;
    font-size: 14.5px;
    text-align: center;
    line-height: 34px;
    letter-spacing: 0.2px;
  }
</style>
</head>
<body>
  <main class="canvas">
    <section class="card card--front" aria-label="Card front">
      <h1 class="front__name">QUELBROOK INSIGHTS</h1>
      <p class="front__tagline">MEASURE , MONITOR , SAVE</p>
    </section>

    <section class="card card--back" aria-label="Card back">
      <div class="back__header">
        <div class="back__mark"></div>
        <p class="back__brand">Quelbrook Insights</p>
      </div>
      <div class="back__contact">
        <p class="contact__name">FIRST NAME LAST NAME</p>
        <p class="contact__line">TITLE</p>
        <p class="contact__line">Address goes here</p>
        <p class="contact__line">+61-3-5550-1842</p>
      </div>
      <footer class="back__footer">www.quelbrook-insights.example</footer>
    </section>
  </main>
</body>
</html>
```